FREE BBQ for life if you win our business with your creative menu design

Looking for a 11x17 size menu. we are a full service BBQ restaurant. We have an upscale environment as well as up scale service. We offer 5 star dinning at a casual price. we are on route 84 and are proud of that. we offer the finest smoked meats. Specializing in smoked pork beef and bison. we have an old barn wood decor. we only use oak to smoke our meats. use a lot of tarnished metal as well as some string nail art. Looking for a menu that goes along our style. i have attached as many pictures as i could to give you a fill of how we do it out here.
PLEASE USE THE 11"X17" MENU TEMPLATE ATTACHED IN THE PROJECT BRIEF.
Target Market(s)
Cool people and there families.
Industry/Entity Type
Business
Requirements
Must have
- I have attached the Current menu we use. File brantlys menu pub. Those are all the Items. There will be some changes as we but together the new menu. The prices are changing. but that should be an easy change as we go.
Nice to have
- We are getting away from the lunch dinner menu and going to an all day menu. so rather than coming with toast or bun we will now be asking as an option. I have attached a menu i tried to make as a sample of how we will be doing it. new menu single page and new menu single page flame. These are ideas i had but could not really make it work. so use them as an idea of what we are looking for but be creative.

```html
<!DOCTYPE html>
<html lang="en">
<head>
<meta charset="utf-8">
<title>Fresh From The Grill – Menu</title>
<link href="https://fonts.googleapis.com/css2?family=Bebas+Neue&family=Alfa+Slab+One&family=Rye&family=Crimson+Text:wght@400;700&family=Oswald:wght@500&display=swap" rel="stylesheet">
<style>
:root{
  --wood-dark:#2c3538;
  --wood-teal:#4e7478;
  --wood-mid:#3a4a4d;
  --panel:rgba(26,26,26,0.86);
  --orange:#f0782a;
  --orange-box:#f37321;
  --title-red:#5a150c;
  --flame:#f7a53a;
  --white:#ffffff;
  --body:#f1ece4;
  --blue:#1864b4;
}
*{margin:0;padding:0;box-sizing:border-box}
html,body{width:927px;height:1200px;overflow:hidden;background:#222}
.menu{position:relative;width:927px;height:1200px;overflow:hidden;font-family:'Crimson Text',serif;color:var(--body)}
.backdrop{position:absolute;inset:0;
  background:
    radial-gradient(ellipse at 50% 15%,rgba(90,130,132,.55),transparent 60%),
    linear-gradient(180deg,var(--wood-teal) 0%,var(--wood-mid) 28%,var(--wood-dark) 60%,#30383a 100%)}
.decor{position:absolute}
.decor-top-left{left:0;top:0;width:260px;height:280px;
  background:radial-gradient(ellipse at 40% 40%,rgba(120,112,108,.55),rgba(120,112,108,0) 70%)}
.decor-right-top{right:0;top:220px;width:180px;height:360px;
  background:radial-gradient(ellipse at 80% 50%,rgba(200,110,50,.5),rgba(60,110,160,.35) 45%,rgba(0,0,0,0) 75%)}
.decor-left-mid{left:0;top:280px;width:140px;height:440px;
  background:radial-gradient(ellipse at 0% 50%,rgba(140,110,130,.55),rgba(0,0,0,0) 70%)}
.decor-right-low{right:0;top:640px;width:150px;height:460px;
  background:radial-gradient(ellipse at 100% 50%,rgba(120,90,110,.5),rgba(0,0,0,0) 70%)}
.decor-plank{left:0;right:0;top:1108px;height:92px;
  background:linear-gradient(180deg,#7a5233 0%,#6b4426 60%,#8c8a86 100%)}
.header{position:absolute;left:0;top:34px;width:927px;text-align:center}
.header-kicker{font-family:'Alfa Slab One',serif;font-size:40px;color:var(--title-red);letter-spacing:1px;margin-left:140px}
.header-title{font-family:'Rye',serif;font-size:120px;line-height:1;margin-top:-6px;margin-left:140px;color:var(--flame);text-shadow:0 0 14px #e0401a,0 0 30px #a3200c}
.panel{position:absolute;left:74px;top:264px;width:780px;height:844px;background:var(--panel);border-radius:22px}
.col{position:absolute}
.h{font-family:'Bebas Neue',sans-serif;color:var(--white);font-size:46px;line-height:.92;letter-spacing:.5px}
.sub{font-size:12px;color:var(--white);font-weight:700;margin:2px 0 8px}
.row{display:flex;justify-content:space-between;font-size:9px;line-height:1;margin-bottom:16px}
.row .name{color:var(--orange);font-weight:700}
.row .price{color:var(--body)}
.item{font-size:8.4px;line-height:1.45;margin-bottom:10px}
.item b{color:var(--orange);display:block}
.note{font-size:8.4px;line-height:1.5;text-align:center;margin:14px 0}
.callout{background:var(--orange-box);color:var(--white);text-align:center;font-size:13px;line-height:1.5;padding:10px 0;margin-top:6px}
.callout strong{font-weight:700}
.step{display:flex;align-items:flex-start;margin-bottom:14px}
.step svg{flex:none;width:52px;height:52px;margin-right:14px}
.step h3{font-family:'Oswald',sans-serif;font-weight:500;font-size:13px;color:var(--white);margin-top:8px}
.step p{font-size:8.4px;line-height:1.45;margin-top:3px}
.loyalty{position:absolute;left:636px;top:904px;width:200px;height:150px}
.loyalty-photo{position:absolute;left:36px;top:0;width:120px;height:120px;border-radius:50%;background:radial-gradient(circle,#6a3a20,#2a160c);border:5px solid var(--white)}
.loyalty-name{position:absolute;left:36px;top:34px;width:120px;text-align:center;font-family:'Crimson Text',serif;font-weight:700;font-size:32px;color:var(--white)}
.loyalty-banner{position:absolute;left:0;top:104px;width:194px;background:var(--blue);color:var(--white);font-family:'Bebas Neue',sans-serif;font-size:17px;text-align:center;padding:2px 0;transform:rotate(-2deg)}
.loyalty-tag{position:absolute;left:38px;top:130px;width:130px;background:var(--orange-box);color:var(--white);font-size:9px;line-height:1.1;text-align:center;padding:3px 0;transform:rotate(-4deg)}
</style>
</head>
<body>
<main class="menu">
  <div class="backdrop" role="img" aria-label="Weathered teal barn wood boards"></div>
  <div class="decor decor-top-left" role="img" aria-label="Tarnished metal star decoration"></div>
  <div class="decor decor-right-top" role="img" aria-label="Blue and orange string nail art"></div>
  <div class="decor decor-left-mid" role="img" aria-label="Tarnished metal sign pieces"></div>
  <div class="decor decor-right-low" role="img" aria-label="Rusted metal letters"></div>
  <div class="decor decor-plank" role="img" aria-label="Barn wood plank and corrugated metal edge"></div>

  <header class="header">
    <div class="header-kicker">FRESH FROM THE</div>
    <div class="header-title">GRILL</div>
  </header>

  <section class="panel"></section>

  <section class="col" style="left:96px;top:326px;width:220px">
    <h2 class="h">Meats in Bulk</h2>
    <div class="sub">Meats Served by the Pound</div>
    <div class="row"><span class="name">Pulled Pork</span><span class="price">$11.99 LB</span></div>
    <div class="row"><span class="name">Sliced Beef</span><span class="price">$11.99 LB</span></div>
    <div class="row"><span class="name">Sliced Pork</span><span class="price">$11.99 LB</span></div>
    <div class="row"><span class="name">Beef Brisket</span><span class="price">$12.99 LB</span></div>
    <div class="row"><span class="name">Smoked Turkey</span><span class="price">$14.99 LB</span></div>
    <div class="row"><span class="name">Smoked Chicken</span><span class="price">$14.99 LB</span></div>
    <div class="row"><span class="name">Bison Brisket</span><span class="price">$16.99 LB</span></div>
    <div class="row"><span class="name">Baby Back Ribs</span><span class="price">$16.99 LB</span></div>
    <div class="row"><span class="name">Toast</span><span class="price">$0.35 each</span></div>
    <div class="row"><span class="name">Buns</span><span class="price">$0.45 each</span></div>
  </section>

  <section class="col" style="left:348px;top:326px;width:234px">
    <h2 class="h">Side Dishes</h2>
    <div style="height:8px"></div>
    <div class="row"><span class="name">Green Chile Creamed Corn</span><span class="price">$4.00 per pint</span></div>
    <div class="row"><span class="name">Potato Salad</span><span class="price">$4.00 per pint</span></div>
    <div class="row"><span class="name">Grilled Veggies</span><span class="price">$4.00 per pint</span></div>
    <div class="row"><span class="name">Baked Beans</span><span class="price">$4.00 per pint</span></div>
    <div class="row"><span class="name">Baked Potato</span><span class="price">$4.00 per pint</span></div>
    <div class="row"><span class="name">Served with butter and cream</span><span class="price" style="width:60px">$1.00</span></div>
    <h2 class="h" style="margin-top:12px">Desserts</h2>
    <div class="item" style="margin-top:6px"><b>Peach Cobbler &amp; Ice Cream</b>$6.00 per person</div>
    <div class="item"><b>Fresh Baked 3oz cookies</b>$3.00 per person</div>
  </section>

  <section class="col" style="left:612px;top:326px;width:224px">
    <h2 class="h">Catering</h2>
    <p class="note">All catered jobs require a week notice to insure we have the meat you want. And the time available for your event.</p>
    <div class="row" style="margin-bottom:4px"><span class="name">Delivery fee Local</span><span class="price" style="width:64px">$10.00</span></div>
    <div class="row" style="margin-bottom:4px"><span class="name">Surrounding areas Delivery</span><span class="price" style="width:64px">$0.50 Per Mile</span></div>
    <div class="row" style="margin-bottom:4px"><span class="name">Plates &amp; Utensils</span><span class="price" style="width:64px">$0.35 PP</span></div>
    <div class="row" style="margin-bottom:4px"><span class="name">Service Fee</span><span class="price" style="width:64px">$65.00 HR</span></div>
    <p class="note">Includes set up, service, and take down of food service area. We supply tables and serving utensils we need for serving our food.</p>
    <div class="callout">Catering business parties<br>and family get-togethers!<br><strong>Call for availability<br>505-555-0148</strong></div>
  </section>

  <section class="col" style="left:96px;top:684px;width:200px">
    <h2 class="h">Appetizer</h2>
    <div style="height:8px"></div>
    <div class="item"><b>King Rings</b>Green Chili battered fried golden crispy 1" thick onion rings. 6.89</div>
    <div class="item"><b>Deep Fried Pickles</b>Crisp dill pickle chips battered and fried to a golden crispy brown 6.89</div>
    <div class="item"><b>Fried Okra</b>Okra is breaded then fried until golden. 6.89</div>
    <div class="item"><b>Green Chili Waffle Fries</b>Crispy waffle-cut Fries, topped with a savory blend of cheese, and New Mexico green chile. 7.49</div>
    <div class="item"><b>KC Wild Wings</b>Big, meaty pork wings, deep fried to a perfect golden brown, tossed in a hot and tangy Buffalo-style sauce, and served with spicy buttermilk ranch dressing on the side. 7.99</div>
    <div class="item"><b>Sampler Platter</b>Two KC Wild Wings, 6oz Fried Pickles, 3 King Rings. 7.99</div>
  </section>

  <section class="col" style="left:344px;top:684px;width:240px">
    <h2 class="h">Create Your<br>Own Wrap</h2>
    <div style="height:14px"></div>
    <div class="step">
      <svg viewBox="0 0 52 52" aria-hidden="true"><polygon points="26,2 32,19 50,19 36,30 41,48 26,37 11,48 16,30 2,19 20,19" fill="none" stroke="var(--orange)" stroke-width="2"/><ellipse cx="26" cy="28" rx="7" ry="5" fill="var(--white)"/></svg>
      <div><h3>PICK YOUR OWN MEAT</h3><p>Pork, beef, chicken, turkey.</p></div>
    </div>
    <div class="step">
      <svg viewBox="0 0 52 52" aria-hidden="true"><polygon points="26,2 32,19 50,19 36,30 41,48 26,37 11,48 16,30 2,19 20,19" fill="none" stroke="var(--orange)" stroke-width="2"/><polygon points="18,33 34,33 34,24 18,28" fill="var(--white)"/></svg>
      <div><h3>PICK YOUR OWN CHEESE</h3><p>Pepper Jack, cheddar, cottage cheese.</p></div>
    </div>
    <div class="step">
      <svg viewBox="0 0 52 52" aria-hidden="true"><polygon points="26,2 32,19 50,19 36,30 41,48 26,37 11,48 16,30 2,19 20,19" fill="none" stroke="var(--orange)" stroke-width="2"/><circle cx="26" cy="29" r="6" fill="var(--white)"/></svg>
      <div><h3>PICK THE ADDITIONALS</h3><p>Lettuce, tomato, pickle, onion, banana peppers, cucumber, grilled veggies and green Chile.</p></div>
    </div>
    <div class="step">
      <svg viewBox="0 0 52 52" aria-hidden="true"><polygon points="26,2 32,19 50,19 36,30 41,48 26,37 11,48 16,30 2,19 20,19" fill="none" stroke="var(--orange)" stroke-width="2"/><rect x="23" y="20" width="6" height="16" rx="2" fill="var(--white)" transform="rotate(35 26 28)"/></svg>
      <div><h3>PICK YOUR OWN SAUCE</h3><p>Spicy Ranch, Reg. Ranch, Blue Cheese, Italian, Sour Cream, Thousand Island, Hot BBQ sauce, Sweet BBQ sauce.</p></div>
    </div>
  </section>

  <section class="col" style="left:608px;top:684px;width:220px">
    <h2 class="h">Drinks</h2>
    <div style="height:8px"></div>
    <div class="item" style="margin-bottom:14px"><b>Lemonade</b>Regular, Strawberry, Watermelon<br>Cherry, Peach 2.59</div>
    <div class="item" style="margin-bottom:14px"><b>Fountain</b>Fizzo, Doc Spice, Root Beer, Lemon Peak, Mountain Zing, Diet Fizzo, Diet Doc Spice 1.89</div>
    <div class="item"><b>Iced Teas</b>Sweetened, Unsweetened 1.89</div>
  </section>

  <aside class="loyalty">
    <div class="loyalty-photo" role="img" aria-label="Smoked meat photo behind app name"></div>
    <div class="loyalty-name">Ember</div>
    <div class="loyalty-banner">JOIN OUR CUSTOMER LOYALTY APP</div>
    <div class="loyalty-tag">Get FREE FOOD when you become a loyal customer.</div>
  </aside>
</main>
</body>
</html>
```